Elevating our current Business Card Design

We want to elevate our current business card with a new design to look like a zenith 300 company. We are a premium lubricant distributor (oil and grease).
We need 2 versions, version 1 is as per the uploaded a copy of our current business card with the English version.
For our Chinese version we need to use the front to be English in English and have the back of the card designed exactly like the front for all info to be in Chinese.
The design template needs to be such that we can amend the template with adding different information for each person's card.
The background colour of the card can be changed- we just need to clearly see all information on the card and logos.
The QJR and Ember steady logos cannot have any colour or display changes- only use the logos attached.
All logos need to be included and all information from the attached current card

```html
<!DOCTYPE html>
<html lang="en">
<head>
<meta charset="utf-8">
<title>Meridian Lube Supply – Business Card</title>
<link rel="stylesheet" href="https://fonts.googleapis.com/css2?family=Ubuntu:wght@500;700&family=Open+Sans:wght@400;600&display=swap">
<style>
  :root {
    --stage: #232323;
    --card: #ffffff;
    --red: #e8302a;
    --red-deep: #a8171f;
    --gold: #f6c02f;
    --gold-deep: #d39a2a;
    --grey: #9a9b9f;
    --ink: #1e1e1e;
    --ember: #1f4a33;
    --badge: #f07a1c;
    --pattern: #f6ecd9;
  }
  * { box-sizing: border-box; margin: 0; padding: 0; }
  html, body { width: 1200px; height: 780px; overflow: hidden; }
  body {
    background: var(--stage);
    font-family: "Open Sans", sans-serif;
    color: var(--ink);
    display: flex;
    align-items: center;
    justify-content: center;
    gap: 40px;
  }
  .card {
    position: relative;
    width: 560px;
    height: 320px;
    background: var(--card);
    border-radius: 22px;
    overflow: hidden;
  }
  .card-bands { position: absolute; inset: 0; width: 100%; height: 100%; }

  .brand {
    position: absolute;
    display: flex;
    align-items: center;
    gap: 12px;
    font-family: "Ubuntu", sans-serif;
    font-weight: 700;
    color: var(--red);
    letter-spacing: -2px;
  }
  .brand-dot { border-radius: 50%; background: var(--gold); }
  .brand--front { left: 150px; top: 62px; font-size: 118px; }
  .brand--front .brand-dot { width: 34px; height: 34px; }
  .brand--back { left: 44px; top: 110px; font-size: 78px; }
  .brand--back .brand-dot { width: 24px; height: 24px; }

  /* front partner row */
  .partner-ember {
    position: absolute; left: 30px; top: 236px;
    display: flex; align-items: center; gap: 6px;
    font-family: "Ubuntu", sans-serif; font-weight: 700; font-size: 13px;
    color: var(--ember); white-space: nowrap;
  }
  .partner-ember .mark { width: 14px; height: 14px; border-radius: 50%; background: var(--ember); }
  .cert {
    position: absolute; width: 30px; height: 30px; border-radius: 50%;
    background: var(--badge); border: 3px solid #c9c9c9;
  }
  .cert--row { left: 158px; top: 228px; }
  .cert--top-a { left: 460px; top: 156px; }
  .cert--top-b { left: 505px; top: 144px; }
  .distributor-box {
    position: absolute; left: 202px; top: 214px;
    border: 1.5px solid var(--red); border-radius: 3px;
    padding: 4px 10px; background: #fff;
    font-family: "Ubuntu", sans-serif; font-weight: 500; font-size: 10px;
    color: var(--red); text-transform: uppercase; line-height: 1.2;
    white-space: nowrap;
  }
  .supplier-block {
    position: absolute; left: 306px; top: 188px;
    background: var(--red); color: #fff;
    padding: 6px 18px; border-radius: 2px;
    font-family: "Ubuntu", sans-serif; font-weight: 700; font-size: 20px;
    letter-spacing: 1px; text-transform: uppercase;
  }

  /* back */
  .pattern-area {
    position: absolute; right: 0; top: 0; width: 250px; height: 250px;
    background: radial-gradient(circle at 70% 45%, var(--pattern) 0%, rgba(246,236,217,0.5) 50%, rgba(255,255,255,0) 75%);
  }
  .contact { position: absolute; left: 318px; top: 40px; }
  .contact-name {
    font-family: "Ubuntu", sans-serif; font-weight: 700; font-size: 28px;
    color: var(--red); line-height: 1.1;
  }
  .contact-role { font-size: 13px; font-weight: 600; margin-bottom: 12px; }
  .contact-list { list-style: none; }
  .contact-list li {
    display: flex; align-items: center; gap: 8px;
    font-size: 12px; line-height: 21px; white-space: nowrap;
  }
  .contact-list svg { width: 12px; height: 12px; flex: none; }
  .address {
    position: absolute; right: 36px; top: 220px;
    font-size: 13px; color: var(--ink); white-space: nowrap;
  }
</style>
</head>
<body>

  <section class="card card--front" aria-label="Card front">
    <svg class="card-bands" viewBox="0 0 560 320" aria-hidden="true">
      <defs>
        <linearGradient id="goldBand" x1="0" y1="1" x2="1" y2="0">
          <stop offset="0" stop-color="var(--gold)"/><stop offset="1" stop-color="var(--gold-deep)"/>
        </linearGradient>
        <linearGradient id="redBand" x1="0" y1="0" x2="1" y2="0">
          <stop offset="0" stop-color="var(--red)"/><stop offset="1" stop-color="var(--red-deep)"/>
        </linearGradient>
      </defs>
      <polygon points="0,302 300,258 262,320 0,320" fill="url(#goldBand)"/>
      <polygon points="306,256 560,200 560,320 270,320" fill="url(#redBand)"/>
    </svg>

    <div class="brand brand--front"><span class="brand-dot"></span>MLS</div>

    <div class="partner-ember"><span class="mark"></span>Ember steady</div>
    <span class="cert cert--row"></span>
    <div class="distributor-box">Meridian<br>Lube Supply</div>
    <div class="supplier-block">Veltrax</div>
    <span class="cert cert--top-a"></span>
    <span class="cert cert--top-b"></span>
  </section>

  <section class="card card--back" aria-label="Card back">
    <div class="pattern-area" role="img" aria-label="Soft gold dot pattern in the background"></div>
    <svg class="card-bands" viewBox="0 0 560 320" aria-hidden="true">
      <defs>
        <linearGradient id="goldBandB" x1="0" y1="1" x2="1" y2="0">
          <stop offset="0" stop-color="var(--gold)"/><stop offset="1" stop-color="var(--gold-deep)"/>
        </linearGradient>
        <linearGradient id="redBandB" x1="0" y1="0" x2="1" y2="0">
          <stop offset="0" stop-color="var(--red)"/><stop offset="1" stop-color="var(--red-deep)"/>
        </linearGradient>
      </defs>
      <polygon points="0,304 320,272 290,320 0,320" fill="url(#goldBandB)"/>
      <polygon points="330,270 560,246 560,320 298,320" fill="url(#redBandB)"/>
      <line x1="262" y1="70" x2="300" y2="232" stroke="var(--ink)" stroke-width="1"/>
    </svg>

    <div class="brand brand--back"><span class="brand-dot"></span>MLS</div>

    <div class="contact">
      <p class="contact-name">Mara Quinlan</p>
      <p class="contact-role">Administration Executive</p>
      <ul class="contact-list">
        <li><svg viewBox="0 0 12 12" aria-hidden="true"><path d="M2 1l2 0 1 3-1.5 1a7 7 0 0 0 3.5 3.5L8 7l3 1v2c0 .6-.4 1-1 1A9 9 0 0 1 1 2c0-.6.4-1 1-1z" fill="var(--red)"/></svg>1300 427 615</li>
        <li><svg viewBox="0 0 12 12" aria-hidden="true"><rect x="3" y="0.5" width="6" height="11" rx="1.2" fill="none" stroke="var(--red)" stroke-width="1.2"/></svg>+61 455 218 907</li>
        <li><svg viewBox="0 0 12 12" aria-hidden="true"><rect x="1" y="4" width="10" height="7" rx="1" fill="var(--red)"/><rect x="3" y="1" width="6" height="3" fill="var(--red)"/></svg>+61 8 9264 3051</li>
        <li><svg viewBox="0 0 12 12" aria-hidden="true"><circle cx="6" cy="6" r="5" fill="none" stroke="var(--red)" stroke-width="1.2"/><path d="M1 6h10M6 1c-2.5 3-2.5 7 0 10M6 1c2.5 3 2.5 7 0 10" fill="none" stroke="var(--red)" stroke-width="1"/></svg>www.meridianlube.com</li>
        <li><svg viewBox="0 0 12 12" aria-hidden="true"><rect x="0.5" y="2" width="11" height="8" rx="1" fill="var(--red)"/><path d="M1 3l5 4 5-4" fill="none" stroke="#fff" stroke-width="1"/></svg>mara.quinlan@meridianlube.com</li>
      </ul>
    </div>

    <p class="address">48 Freight Way Ashfield, WA 6054</p>
  </section>

</body>
</html>
```